Quorbelline.io - Please redesign to make it look better from current design

We already have the current website, that you can access but we think it can improve from current version.
Quorbelline is a cryptocurrency hedge fund that allow you to participate in the hedge fund with cryptocurrency such as eth.
At current phase, we are doing an ICO, then we want to make sure that the website it looks professional, beautiful and trustable enough for investors after looking at our website.
Target Market(s)
Investors
Industry/Entity Type
Investment
Coding
Coded - Design and coding required
Number of Pages Required
1 page
Look and feel
Each slider illustrates characteristics of the customer's brand and the style your logo design should communicate.

```html
<!DOCTYPE html>
<html lang="en">
<head>
<meta charset="utf-8">
<title>Quorbelline – Digital Asset Management</title>
<link rel="stylesheet" href="https://fonts.googleapis.com/css2?family=Lato:wght@400;700&family=Open+Sans:wght@400;600&display=swap">
<style>
:root{
  --navy:#0d56a8;
  --navy-deep:#0a4a97;
  --heading:#1a4f9c;
  --sky:#2ea2da;
  --sky-deep:#2592cc;
  --accent:#2a8fd0;
  --ink:#333;
  --muted:#555;
  --white:#fff;
  --rule:#d6d6d6;
}
*{margin:0;padding:0;box-sizing:border-box}
html,body{width:1200px;height:3066px;overflow:hidden}
body{position:relative;background:var(--white);font-family:'Open Sans',Arial,sans-serif;color:var(--ink)}
.section{position:absolute;left:0;width:1200px}
.abs{position:absolute}
.center{text-align:center;left:0;width:1200px}
.rule{position:absolute;height:2px}

/* Hero */
.hero{top:0;height:630px;background:linear-gradient(135deg,#0f62b8 0%,var(--navy) 55%,var(--navy-deep) 100%);color:var(--white)}
.brand{left:98px;top:34px;display:flex;align-items:center;gap:12px;font-family:'Lato',sans-serif;font-weight:700;font-size:26px;color:var(--white)}
.brand-dot{width:22px;height:22px;border-radius:50%;background:var(--white)}
.nav{right:100px;top:52px;display:flex;gap:40px;font-family:'Lato',sans-serif;font-size:16px;letter-spacing:.3px}
.nav-rule{left:98px;top:126px;width:1002px;height:2px;background:rgba(255,255,255,.85)}
.hero-title{left:98px;top:192px;font-family:'Lato',sans-serif;font-weight:700;font-size:58px;letter-spacing:1px}
.hero-sub{left:98px;top:270px;font-family:'Lato',sans-serif;font-weight:700;font-size:37px}
.hero-text{left:98px;top:344px;width:560px;font-size:15.5px;font-weight:600;line-height:27px}
.btn-outline-light{left:98px;top:445px;width:111px;height:50px;border:2px solid var(--white);font-family:'Lato',sans-serif;font-weight:700;font-size:16px;display:flex;align-items:center;justify-content:center}
.dots{left:98px;top:527px;display:flex;gap:4px}
.dots span{width:14px;height:14px;border-radius:50%;border:2px solid var(--white)}
.dots span.on{background:var(--white)}
.hero-art{left:680px;top:165px;width:470px;height:450px;border-radius:40px 40px 0 0;background:linear-gradient(160deg,#3fa35b 0%,#e2b53c 45%,#2f3f55 100%);opacity:.85}

/* About */
.about{top:630px;height:408px}
.h2{font-family:'Lato',sans-serif;font-weight:700;font-size:29px}
.about .h2{top:60px;color:var(--heading)}
.about .rule{top:116px;left:560px;width:80px;background:var(--heading)}
.about-text{top:160px;left:123px;width:955px;text-align:center;font-size:13.5px;line-height:22px;color:var(--muted)}
.btn-solid{left:485px;top:300px;width:110px;height:45px;background:var(--heading);color:var(--white);font-family:'Lato',sans-serif;font-weight:700;font-size:14px;display:flex;align-items:center;justify-content:center}
.btn-outline-dark{left:606px;top:300px;width:110px;height:45px;border:2px solid #333;font-family:'Lato',sans-serif;font-size:14px;display:flex;align-items:center;justify-content:center}

/* Team */
.team{top:1038px;height:679px;background:linear-gradient(135deg,#35a9df 0%,var(--sky) 50%,var(--sky-deep) 100%);color:var(--white)}
.team .h2{top:57px}
.team .rule{top:116px;left:560px;width:80px;background:var(--white)}
.member{top:178px;width:354px;height:419px;text-align:center}
.member.featured{background:var(--white);color:var(--accent)}
.portrait{position:absolute;left:105px;top:14px;width:144px;height:144px;border-radius:50%;border:3px solid #333;background:linear-gradient(160deg,#8a7a6a,#3c3a3a)}
.member.featured .portrait{border-color:#ddd;background:linear-gradient(160deg,#c9d4c6,#6c6a5e)}
.member-name{position:absolute;top:184px;left:0;width:100%;font-family:'Lato',sans-serif;font-weight:700;font-size:22px}
.member-role{position:absolute;top:229px;left:0;width:100%;font-family:'Lato',sans-serif;font-weight:700;font-size:17px}
.member-bio{position:absolute;top:272px;left:52px;width:250px;font-size:13.5px;line-height:21px}

/* Process */
.process{top:1717px;height:603px}
.process .h2{left:98px;top:64px;color:var(--heading)}
.process .rule{left:98px;top:115px;width:94px;background:var(--heading)}
.h3{font-family:'Lato',sans-serif;font-size:23px;color:var(--accent)}
.process-text{left:98px;width:552px;font-size:13.5px;line-height:21px;color:var(--ink)}
.process-art{left:740px;top:40px;width:460px;height:563px;border-radius:200px 0 0 0;background:linear-gradient(170deg,#e8c15a 0%,#f3dfb4 45%,#c7541f 100%);opacity:.85}

/* CTA */
.cta{top:2320px;height:302px;background:linear-gradient(135deg,#2f78c7 0%,#2a6fbe 60%,#2464b0 100%);color:var(--white)}
.cta .h2{top:58px;font-size:28px}
.cta .rule{top:122px;left:545px;width:110px;background:var(--white)}
.btn-whitepaper{left:435px;top:174px;width:328px;height:56px;border:2px solid var(--white);font-family:'Lato',sans-serif;font-size:19px;display:flex;align-items:center;justify-content:center}

/* Contact */
.contact{top:2622px;height:444px}
.contact .h2{top:56px;color:var(--heading)}
.contact .rule{top:106px;left:560px;width:82px;background:var(--heading)}
.pin{left:576px;top:158px;width:48px;height:48px;border:2px solid var(--heading);border-radius:50%;display:flex;align-items:center;justify-content:center}
.address{top:230px;font-size:14px;line-height:26px;color:var(--ink)}
.foot-rule{left:98px;top:361px;width:1002px;height:1px;background:var(--rule)}
.copyright{top:392px;font-size:13.5px;color:var(--ink)}
</style>
</head>
<body>

<header class="section hero">
  <div class="abs brand"><span class="brand-dot"></span>Quorbelline</div>
  <nav class="abs nav"><span>HOME</span><span>ABOUT US</span><span>SERVICES</span><span>BLOG</span><span>CONTACT US</span></nav>
  <div class="abs nav-rule"></div>
  <h1 class="abs hero-title">QUORBELLINE</h1>
  <div class="abs hero-sub">Digital Asset Management</div>
  <p class="abs hero-text">Quorbelline enable companies and investors to facilities business operation in modern digital world, including asset management on hedge fund strategy model.</p>
  <div class="abs btn-outline-light">Read More</div>
  <div class="abs dots"><span class="on"></span><span></span><span></span><span></span><span></span></div>
  <div class="abs hero-art" role="img" aria-label="Illustration of hands holding a wallet, banknotes, coins, a receipt and a bank card"></div>
</header>

<section class="section about">
  <h2 class="abs center h2">About Quorbelline</h2>
  <div class="rule"></div>
  <p class="abs about-text">Quorbelline process and manages on hedge fund strategy models which invests in a diversified portfolio of blockchain tokens. Blockchain tokens are emerging which add a monetary incentive layer to p2p protocols and facilitate equity crowdfunding that anyone in the world can participate in. This means open source software developers can monetize their networks at the protocol level and users of the network are the equity owners of the network. For this conditions, returns will go to holders of the tokens.</p>
  <div class="abs btn-solid">Read More</div>
  <div class="abs btn-outline-dark">Contact Us</div>
</section>

<section class="section team">
  <h2 class="abs center h2">Our Executive Team</h2>
  <div class="rule"></div>
  <article class="abs member" style="left:70px">
    <div class="portrait" role="img" aria-label="Portrait photo of the director"></div>
    <div class="member-name">Teerapat Wongsiri</div>
    <div class="member-role">Director</div>
    <p class="member-bio">As a hedge fund manager. Wongsiri is the Chief Executive Officer of Halvard Capital LLC, an investment manager of Ostrava Metal Fund SP (Long-Short Equity Fund, investing in U.S. Stock Market).</p>
  </article>
  <article class="abs member featured" style="left:423px">
    <div class="portrait" role="img" aria-label="Portrait photo of the director"></div>
    <div class="member-name">Teerapat Wongsiri</div>
    <div class="member-role">Director</div>
    <p class="member-bio">As a hedge fund manager. Wongsiri is the Chief Executive Officer of Halvard Capital LLC, an investment manager of Ostrava Metal Fund SP (Long-Short Equity Fund, investing in U.S. Stock Market).</p>
  </article>
  <article class="abs member" style="left:771px">
    <div class="portrait" role="img" aria-label="Portrait photo of the director"></div>
    <div class="member-name">Teerapat Wongsiri</div>
    <div class="member-role">Director</div>
    <p class="member-bio">As a hedge fund manager. Wongsiri is the Chief Executive Officer of Halvard Capital LLC, an investment manager of Ostrava Metal Fund SP (Long-Short Equity Fund, investing in U.S. Stock Market).</p>
  </article>
</section>

<section class="section process">
  <h2 class="abs h2">Our Process</h2>
  <div class="rule"></div>
  <h3 class="abs h3" style="left:98px;top:142px">Hedge Fund Model</h3>
  <p class="abs process-text" style="top:193px;text-align:justify">Quorbelline run on closed-end fund (CEF) model which offers its shares to investors and utilize the fund to speculate and invest in the innovative blockchain tokens. Quorbelline will charge an upfront annual operation fee 4% of the money raised during the ICO. After that, the fund will charge a quarterly performance of 50% on the net profit made.</p>
  <h3 class="abs h3" style="left:98px;top:338px">Net Profit Distribution</h3>
  <p class="abs process-text" style="top:388px">50 % of net profit is distributed to investors<br>0 – 5 % net profit &gt; 0% performance fee<br>5 – 10% net profit &gt; 5% performance fee<br>10-15 % net profit &gt; 13% performance fee<br>&gt; 15% net profit &gt; 15% performance fee<br>The remainder (50% minus performance fee, so at least 35%) is reinvested</p>
  <div class="abs process-art" role="img" aria-label="Illustration of a hand holding stacked coins with a growing plant and gold coins"></div>
</section>

<section class="section cta">
  <h2 class="abs center h2">FOR MORE INFORMATION</h2>
  <div class="rule"></div>
  <div class="abs btn-whitepaper">DOWNLOAD WHITEPAPER</div>
</section>

<footer class="section contact">
  <h2 class="abs center h2">Contact Us</h2>
  <div class="rule"></div>
  <div class="abs pin">
    <svg width="16" height="22" viewBox="0 0 16 22" aria-hidden="true"><path d="M8 1C4.1 1 1 4.1 1 8c0 5.2 7 13 7 13s7-7.8 7-13c0-3.9-3.1-7-7-7z" fill="none" stroke="#1a4f9c" stroke-width="2"/><circle cx="8" cy="8" r="2.5" fill="#1a4f9c"/></svg>
  </div>
  <p class="abs center address">Suites 05-15, 13A/F., North Tower, Meridian Trade Centre,<br>Lantern Bay, 42, Harbour Road, Wan Sai Kok,<br>Kowloon, Hong Kong.</p>
  <div class="abs foot-rule"></div>
  <p class="abs center copyright">Copyrights @ 2017 Quorbelline. All Rights Reserved.</p>
</footer>

</body>
</html>
```